Company Website for Varnoth Signal, an open source data analytics company focused on relationship and li

I need a company/brand website for our new startup, Varnoth Signal LLC. We are a company focused on using life pattern analysis techniques, looking at relationships and how relationships, attributes, and activity cluster to infer aggregate information about individuals and groups. Our focus is on improving the digital advertising market.

We have a company logo which I will upload shortly.

Target Market(s)

Digital Advertising

Number of Pages Required

3 page

Font styles to use
Sans Serif

Requirements
Must have
• An main page, about us, contact page.
Nice to have
• Varnoth Signal relies on state of the art analytics applied to a the digital marketing space. While it is heavy in science, we also understand the art of influence. The website should have a scientific edge but also a flair that illustrates our focus on applying the hard science and analytics to influencing the behavior of people.

```html
<!DOCTYPE html>
<html lang="en">
<head>
<meta charset="utf-8">
<title>Varnoth Signal</title>
<link href="https://fonts.googleapis.com/css2?family=Montserrat:wght@300;400;700;800&family=Open+Sans:wght@400;600;700&display=swap" rel="stylesheet">
<style>
:root{
  --blue:#1e9ad6;
  --orange:#f07b1f;
  --ink:#1d1d1d;
  --text:#333;
  --muted:#555;
  --light:#f3f1f1;
  --rule:#b5b5b5;
  --footer:#232323;
  --white:#fff;
}
*{margin:0;padding:0;box-sizing:border-box}
html,body{width:1200px;height:3871px;overflow:hidden}
body{font-family:"Open Sans",Arial,sans-serif;color:var(--text);background:var(--white);position:relative}
.abs{position:absolute}
.head{font-family:"Montserrat",Arial,sans-serif}
.btn{display:inline-block;background:var(--orange);color:var(--white);font-family:"Montserrat",Arial,sans-serif;font-weight:700;font-size:13px;text-align:center;letter-spacing:.5px}
.brand{font-family:"Montserrat",Arial,sans-serif;font-weight:800;color:var(--blue);display:flex;align-items:center;gap:10px;white-space:nowrap}
.brand .dot{background:var(--orange);border-radius:50%;flex:none}
.rule{height:3px;background:var(--rule);width:40px;margin:14px auto 0}

/* header */
.site-header{left:0;top:0;width:1200px;height:129px}
.follow{left:705px;top:36px;font-size:11px;font-weight:700;font-family:"Montserrat",Arial,sans-serif;color:var(--ink);display:flex;align-items:center;gap:6px}
.follow span.soc{width:24px;height:24px;border-radius:50%;display:inline-block}
.search{left:913px;top:30px;width:152px;height:28px;border:1px solid #ccc;font-size:10px;color:#777;padding:7px 10px}
.nav{right:132px;top:84px;display:flex;gap:6px;font-family:"Montserrat",Arial,sans-serif;font-weight:700;font-size:12.5px;color:var(--ink)}
.nav a{padding:6px 11px;text-decoration:none;color:inherit}
.nav a.active{background:var(--orange);color:var(--white)}

/* hero */
.hero-art{left:0;top:129px;width:700px;height:537px;background:linear-gradient(135deg,#d8d8d6 0%,#cbcbc9 50%,#c2c2c0 100%)}
.hero-person{left:700px;top:129px;width:500px;height:537px;background:linear-gradient(180deg,#b7b4b0,#e8e6e3 60%,#c8c6c2)}
.hero-arrow{width:34px;height:40px;background:#3a3a3a;top:376px;display:flex;align-items:center;justify-content:center}

/* welcome */
.welcome-kicker{left:185px;top:745px;font-size:25px;font-weight:800;color:var(--ink)}
.welcome-title{left:183px;top:780px;font-size:44px;font-weight:800;color:var(--blue);letter-spacing:.5px}
.welcome-rule{left:185px;top:848px;width:280px;height:2px;background:var(--rule)}
.welcome-copy{left:185px;top:893px;width:415px;font-size:15px;line-height:1.5;color:var(--text)}
.tile{width:100px;height:100px;background:var(--orange);transform:rotate(20deg);display:flex;align-items:center;justify-content:center}
.tile svg{transform:rotate(-20deg)}
.tile-label{font-family:"Montserrat",Arial,sans-serif;font-weight:700;font-size:12px;color:var(--ink);white-space:nowrap}

/* services */
.services{left:0;top:1156px;width:1200px;height:666px;background:var(--light)}
.sec-title{width:1200px;text-align:center;font-family:"Montserrat",Arial,sans-serif;font-weight:800;font-size:27px;color:var(--ink)}
.svc{width:230px;font-size:12.5px;line-height:1.3;color:var(--muted)}
.svc b{display:block;color:var(--ink);font-size:13px;margin-bottom:6px}
.svc.left{text-align:right}
.svc-icon{width:60px;height:60px;background:var(--blue);display:flex;align-items:center;justify-content:center}
.svc-line{height:1px;background:#d6d4d4;width:270px}
.tablet{left:462px;top:1340px;width:268px;height:380px;background:#1b1b1b;border-radius:22px;border:3px solid #9a9a9a}
.tablet-screen{left:20px;top:26px;width:222px;height:305px;background:#060606;display:flex;align-items:center;justify-content:center}

/* life pattern */
.pattern{left:0;top:1822px;width:1200px;height:464px;background:linear-gradient(120deg,#2b2e31 0%,#1d2024 50%,#2f3a3a 100%);color:var(--white);text-align:center}

/* blog */
.card{top:2495px;width:280px;height:380px;background:var(--white);box-shadow:0 2px 10px rgba(0,0,0,.18)}
.card-img{width:280px;height:188px}
.card h3{font-family:"Montserrat",Arial,sans-serif;font-weight:800;font-size:15px;line-height:1.25;color:var(--ink);margin:26px 30px 10px}
.card p{font-size:13px;line-height:1.4;color:var(--text);margin:0 30px 20px}
.card .btn{margin-left:30px;font-size:10.5px;padding:6px 0;width:85px}
.chev{top:2660px}

/* open source */
.os-img{left:0;top:2972px;width:635px;height:527px;background:linear-gradient(135deg,#2b3440,#5b6a7b 45%,#c9d2da 70%,#8a94a0)}
.os-bg{left:635px;top:2972px;width:565px;height:527px;background:var(--light)}
.os-title{left:722px;top:3126px;font-size:29px;font-weight:800;line-height:1.15;color:var(--ink)}
.os-rule{left:722px;top:3200px;width:80px;height:2px;background:var(--rule)}
.os-copy{left:722px;top:3218px;width:350px;font-size:13px;line-height:1.4;color:var(--text)}

/* footer */
.footer{left:0;top:3499px;width:1200px;height:372px;background:var(--footer);color:#ddd;font-size:11.5px}
.f-head{font-family:"Montserrat",Arial,sans-serif;font-weight:700;font-size:12px;color:var(--white)}
.f-list{line-height:1.55}
.f-row{display:flex;gap:10px;align-items:flex-start;margin-bottom:14px}
.f-soc{display:flex;gap:10px;align-items:center;margin-bottom:16px}
.f-soc span{width:22px;height:22px;border-radius:50%;background:#3b5b9c}
.copyright{width:1200px;text-align:center;top:3812px;left:0;font-size:11px;color:#ddd}
</style>
</head>
<body>

<!-- Header -->
<header class="abs site-header">
  <div class="abs brand" style="left:132px;top:38px;font-size:27px"><span class="dot" style="width:16px;height:16px"></span>Varnoth Signal</div>
  <div class="abs follow">FOLLOW US
    <span class="soc" style="background:#3b5998" role="img" aria-label="Friendloop"></span>
    <span class="soc" style="background:#1da1f2" role="img" aria-label="Chirpline"></span>
    <span class="soc" style="background:#0e5a8a" role="img" aria-label="Workgraph"></span>
  </div>
  <div class="abs search">SEARCH
    <svg class="abs" style="right:8px;top:8px" width="11" height="11" viewBox="0 0 11 11"><circle cx="4.5" cy="4.5" r="3.5" fill="none" stroke="#777" stroke-width="1.4"/><line x1="7" y1="7" x2="10" y2="10" stroke="#777" stroke-width="1.4"/></svg>
  </div>
  <nav class="abs nav">
    <a class="active">HOME</a><a>ABOUT US</a><a>SOLUTIONS</a><a>SERVICES</a><a>BLOG</a><a>CONTACT US</a>
  </nav>
</header>

<!-- Hero -->
<div class="abs hero-art" role="img" aria-label="Illustration of a rising bar chart with data analytics and lifestyle behaviors banners"></div>
<div class="abs hero-person" role="img" aria-label="Photo of a thoughtful businesswoman in glasses"></div>
<div class="abs hero-arrow" style="left:0"><svg width="12" height="16" viewBox="0 0 12 16"><polygon points="10,1 2,8 10,15" fill="#fff"/></svg></div>
<div class="abs hero-arrow" style="right:0"><svg width="12" height="16" viewBox="0 0 12 16"><polygon points="2,1 10,8 2,15" fill="#fff"/></svg></div>

<!-- Welcome -->
<section>
  <h2 class="abs head welcome-kicker">WELCOME TO</h2>
  <h1 class="abs head welcome-title">VARNOTH SIGNAL</h1>
  <div class="abs welcome-rule"></div>
  <p class="abs welcome-copy">Lorem Ipsum is simply dummy text of the printing and typesetting industry. Lorem Ipsum has been the industry's standard dummy text ever since the 1500s, when an unknown printer took a galley of type and scrambled it to make a type specimen book.</p>
  <span class="abs btn" style="left:189px;top:1035px;width:120px;padding:10px 0">READ MORE</span>

  <div class="abs tile" style="left:755px;top:750px"><svg width="44" height="44" viewBox="0 0 44 44" fill="none" stroke="#fff" stroke-width="3"><path d="M10 8 l7 0 3 8 -4 3 q4 8 11 11 l3 -4 8 3 0 7 q-20 2 -28 -28z"/><rect x="24" y="4" width="16" height="11" rx="2"/></svg></div>
  <div class="abs tile" style="left:915px;top:810px"><svg width="46" height="46" viewBox="0 0 46 46" fill="none" stroke="#fff" stroke-width="3"><circle cx="23" cy="21" r="15"/><path d="M14 33 l-4 8 10-5"/><circle cx="17" cy="21" r="1.5" fill="#fff"/><circle cx="23" cy="21" r="1.5" fill="#fff"/><circle cx="29" cy="21" r="1.5" fill="#fff"/></svg></div>
  <div class="abs tile" style="left:715px;top:910px"><svg width="46" height="46" viewBox="0 0 46 46" fill="none" stroke="#fff" stroke-width="3"><circle cx="23" cy="23" r="17"/><path d="M15 26 q8 8 16 0"/><circle cx="17" cy="18" r="2" fill="#fff"/><circle cx="29" cy="18" r="2" fill="#fff"/></svg></div>
  <div class="abs tile" style="left:875px;top:965px"><svg width="46" height="46" viewBox="0 0 46 46" fill="none" stroke="#fff" stroke-width="3"><rect x="6" y="30" width="6" height="10"/><rect x="16" y="24" width="6" height="16"/><rect x="26" y="18" width="6" height="22"/><polyline points="6,22 18,14 26,16 40,6"/><polyline points="33,6 40,6 40,13"/></svg></div>
  <span class="abs tile-label" style="left:725px;top:735px;transform:rotate(20deg)">SUPPORT</span>
  <span class="abs tile-label" style="left:1022px;top:930px;transform:rotate(20deg)">HELP</span>
  <span class="abs tile-label" style="left:735px;top:1022px;transform:rotate(-20deg)">SATISFACTION</span>
  <span class="abs tile-label" style="left:950px;top:1080px;transform:rotate(-20deg)">MISSION</span>
</section>

<!-- Services -->
<section class="abs services"></section>
<h2 class="abs sec-title" style="left:0;top:1217px">OUR SERVICES<div class="rule"></div></h2>

<div class="abs svc left" style="left:95px;top:1352px"><b>Lorem Ipsum is simply</b>Lorem Ipsum is simply dummy text of the printing and typeset ting Industry ditors now use</div>
<div class="abs svc left" style="left:95px;top:1488px"><b>Lorem Ipsum is simply</b>Lorem Ipsum is simply dummy text of the printing and typeset ting Industry ditors now use</div>
<div class="abs svc left" style="left:95px;top:1624px"><b>Lorem Ipsum is simply</b>Lorem Ipsum is simply dummy text of the printing and typeset ting Industry ditors now use</div>
<div class="abs svc" style="left:872px;top:1352px"><b>Lorem Ipsum is simply</b>Lorem Ipsum is simply dummy text of the printing and typeset ting Industry ditors now use</div>
<div class="abs svc" style="left:872px;top:1488px"><b>Lorem Ipsum is simply</b>Lorem Ipsum is simply dummy text of the printing and typeset ting Industry ditors now use</div>
<div class="abs svc" style="left:872px;top:1624px"><b>Lorem Ipsum is simply</b>Lorem Ipsum is simply dummy text of the printing and typeset ting Industry ditors now use</div>
<div class="abs svc-line" style="left:140px;top:1462px"></div>
<div class="abs svc-line" style="left:140px;top:1598px"></div>
<div class="abs svc-line" style="left:790px;top:1462px"></div>
<div class="abs svc-line" style="left:790px;top:1598px"></div>

<div class="abs svc-icon" style="left:355px;top:1362px"><svg width="32" height="32" viewBox="0 0 32 32" fill="none" stroke="#fff" stroke-width="2"><circle cx="16" cy="16" r="13"/><circle cx="16" cy="12" r="4"/><path d="M9 24 q7-8 14 0"/></svg></div>
<div class="abs svc-icon" style="left:355px;top:1498px"><svg width="32" height="32" viewBox="0 0 32 32" fill="none" stroke="#fff" stroke-width="2"><rect x="3" y="5" width="26" height="18"/><polyline points="6,18 11,12 15,16 20,9 26,14"/><line x1="12" y1="28" x2="20" y2="28"/></svg></div>
<div class="abs svc-icon" style="left:355px;top:1634px"><svg width="32" height="32" viewBox="0 0 32 32" fill="none" stroke="#fff" stroke-width="2"><rect x="3" y="4" width="26" height="19"/><line x1="8" y1="10" x2="24" y2="10"/><line x1="8" y1="15" x2="20" y2="15"/><line x1="16" y1="23" x2="16" y2="29"/><line x1="10" y1="29" x2="22" y2="29"/></svg></div>
<div class="abs svc-icon" style="left:780px;top:1362px"><svg width="32" height="32" viewBox="0 0 32 32" fill="none" stroke="#fff" stroke-width="2"><rect x="8" y="2" width="16" height="28" rx="2"/><polyline points="12,17 15,20 21,12"/></svg></div>
<div class="abs svc-icon" style="left:780px;top:1498px"><svg width="32" height="32" viewBox="0 0 32 32" fill="none" stroke="#fff" stroke-width="2"><rect x="6" y="4" width="20" height="25"/><line x1="12" y1="11" x2="22" y2="11"/><line x1="12" y1="17" x2="22" y2="17"/><line x1="12" y1="23" x2="22" y2="23"/><circle cx="9.5" cy="11" r="1" fill="#fff"/><circle cx="9.5" cy="17" r="1" fill="#fff"/><circle cx="9.5" cy="23" r="1" fill="#fff"/></svg></div>
<div class="abs svc-icon" style="left:780px;top:1634px"><svg width="32" height="32" viewBox="0 0 32 32" fill="none" stroke="#fff" stroke-width="2"><path d="M4 5 h24 v17 h-14 l-6 6 v-6 h-4z"/><circle cx="12" cy="13" r="1.5" fill="#fff"/><circle cx="20" cy="13" r="1.5" fill="#fff"/></svg></div>

<div class="abs tablet">
  <div class="abs tablet-screen"><div class="brand" style="font-size:20px"><span class="dot" style="width:10px;height:10px"></span>Varnoth Signal</div></div>
</div>

<!-- Life pattern -->
<section class="abs pattern" role="img" aria-label="Dimmed photo of a workspace with a monitor showing data">
  <h2 class="head" style="margin-top:98px;font-weight:300;font-size:37px;letter-spacing:2px">LIFE PATTERN</h2>
  <h2 class="head" style="font-weight:800;font-size:37px;letter-spacing:1px;margin-top:2px">ANALYSIS TECHNIQUES</h2>
  <p style="width:500px;margin:24px auto 0;font-size:15px;line-height:1.55">But I must explain to you how all this mistaken idea of denoupleasure and praising pain was born and I will give you a complete account of the system, and expound the actual.</p>
  <span class="btn" style="margin-top:30px;width:150px;padding:13px 0;font-size:14px">READ MORE</span>
</section>

<!-- Blog -->
<h2 class="abs sec-title" style="left:0;top:2367px">LATEST BLOG<div class="rule"></div></h2>
<svg class="abs chev" style="left:80px" width="16" height="30" viewBox="0 0 16 30"><polyline points="14,2 2,15 14,28" fill="none" stroke="#999" stroke-width="2"/></svg>
<svg class="abs chev" style="left:1086px" width="16" height="30" viewBox="0 0 16 30"><polyline points="2,2 14,15 2,28" fill="none" stroke="#999" stroke-width="2"/></svg>

<article class="abs card" style="left:134px">
  <div class="card-img" role="img" aria-label="Photo of a man in glasses thinking" style="background:linear-gradient(135deg,#9ea1a4,#d0d1d2)"></div>
  <h3>BUT I MUST EXPLAIN TO HOW ALL THIS MIST</h3>
  <p>At vero eos et accusamus et iusto odio dignissimos ducimus.</p>
  <span class="btn">READ MORE</span>
</article>
<article class="abs card" style="left:463px">
  <div class="card-img" role="img" aria-label="Photo of hands holding a tablet with charts" style="background:linear-gradient(135deg,#4a3c32,#c9b8a6 55%,#e8e2dc)"></div>
  <h3>BUT I MUST EXPLAIN TO HOW ALL THIS MIST</h3>
  <p>At vero eos et accusamus et iusto odio dignissimos ducimus.</p>
  <span class="btn">READ MORE</span>
</article>
<article class="abs card" style="left:789px">
  <div class="card-img" role="img" aria-label="Photo of a man working among glowing data screens" style="background:linear-gradient(135deg,#0f1f44,#2e5ca8 55%,#6f9fd8)"></div>
  <h3>BUT I MUST EXPLAIN TO HOW ALL THIS MIST</h3>
  <p>At vero eos et accusamus et iusto odio dignissimos ducimus.</p>
  <span class="btn">READ MORE</span>
</article>

<!-- Open source -->
<div class="abs os-img" role="img" aria-label="Photo of a tablet displaying an analytics dashboard"></div>
<div class="abs os-bg"></div>
<h2 class="abs head os-title">OPEN SOURCE<br>DATA ANALYTICS</h2>
<div class="abs os-rule"></div>
<p class="abs os-copy">On the other hand, we denounce with righteous indignation and dislike men who are so beguiled and demoralized by the charms of pleasure of the moment, so blinded by desire, that they cannot foresee the pain and trouble that are bound to ensue; and equal blame belongs to those who fail in their duty through weakness of will, which is the same.</p>
<span class="abs btn" style="left:722px;top:3358px;width:120px;padding:10px 0">READ MORE</span>

<!-- Footer -->
<footer class="abs footer">
  <div class="abs brand" style="left:152px;top:128px;font-size:30px"><span class="dot" style="width:18px;height:18px"></span>Varnoth Signal</div>

  <div class="abs" style="left:468px;top:62px;width:200px">
    <div class="f-head" style="margin-bottom:22px">CONTACT US</div>
    <div class="f-row"><svg width="10" height="14" viewBox="0 0 10 14"><path d="M5 0 a5 5 0 0 1 5 5 c0 4 -5 9 -5 9 s-5 -5 -5 -9 a5 5 0 0 1 5 -5z" fill="#fff"/><circle cx="5" cy="5" r="2" fill="#232323"/></svg><span class="f-list">518 Meridian Road<br>Halden, IL 60499</span></div>
    <div class="f-row"><svg width="12" height="12" viewBox="0 0 12 12"><path d="M1 1 h3 l1.5 3 -1.5 1 q1.5 3 4 4 l1 -1.5 3 1.5 v3 q-9 0 -11 -11z" fill="#fff"/></svg><span>555.014.2290</span></div>
    <div class="f-row"><svg width="12" height="10" viewBox="0 0 12 10"><rect x="0" y="0" width="12" height="10" fill="#fff"/><polyline points="0,0 6,5 12,0" fill="none" stroke="#232323" stroke-width="1.2"/></svg><span>hello@varnothsignal.com</span></div>
  </div>

  <div class="abs" style="left:725px;top:62px">
    <div class="f-head" style="margin-bottom:22px">MENU</div>
    <div class="f-list">HOME<br>ABOUT US<br>SOLUTIONS<br>SERVICES<br>BLOG<br>CONTACT US</div>
  </div>

  <div class="abs" style="left:928px;top:62px">
    <div class="f-head" style="margin-bottom:22px">CONNECT WITH US</div>
    <div class="f-soc"><span></span>Friendloop</div>
    <div class="f-soc"><span style="background:#1da1f2"></span>Chirpline</div>
    <div class="f-soc"><span style="background:#0e5a8a"></span>Workgraph</div>
  </div>
</footer>
<p class="abs copyright">Copyrights @ 2018 All Rights Reserved</p>

</body>
</html>
```